Visit card

Industry/Entity Type

Health Care

Contact Information for Business Card

O VITALIS SYSTEMS
Odile Brevard - chef de Projet

Requirements
Must have
• 318 Gaston Lemaire Street 59710 VERLANCOURT Tel: 33 (0) 327 481 605 Mobile: 06 42 19 37 64 Web: www.quorvexsystems.example Contact: o.brevard@o-vitalissystems.example
Should not have
• Respect for color

```html
<!DOCTYPE html>
<html lang="fr">
<head>
<meta charset="utf-8">
<title>O Vitalis Systems — Business Card</title>
<link rel="stylesheet" href="https://fonts.googleapis.com/css2?family=Open+Sans:wght@400;600;700&display=swap">
<style>
  :root {
    --bg: #e9e7e4;
    --charcoal: #3d3d3f;
    --charcoal-deep: #2f2f31;
    --red: #e0232f;
    --ink: #3a3a3c;
    --rule: #8a8a8c;
    --paper: #fbfbfb;
    --white: #ffffff;
  }
  * { margin: 0; padding: 0; box-sizing: border-box; }
  html, body {
    width: 1200px; height: 1021px; overflow: hidden;
    background: var(--bg);
    font-family: "Open Sans", Arial, sans-serif;
  }
  .stage { position: relative; width: 1200px; height: 1021px; }
  .card {
    position: absolute; left: 220px; width: 760px; height: 434px;
    overflow: hidden;
    box-shadow: 0 6px 18px rgba(0,0,0,.18);
  }

  /* Back side */
  .card--back { top: 60px; background: var(--charcoal); }
  .card--back .brand-disc {
    position: absolute; left: 470px; top: 30px; width: 360px; height: 360px;
    border-radius: 50%;
    background: radial-gradient(circle at 35% 30%, #5a5a5c, #333335 70%);
  }
  .card--back .brand-name {
    position: absolute; left: 60px; top: 200px;
    font-size: 34px; font-weight: 700; letter-spacing: 1px; color: var(--white);
  }
  .card--back .website {
    position: absolute; left: 62px; top: 258px;
    font-size: 16px; color: var(--white); letter-spacing: .3px;
  }
  .card--back .website span { color: var(--red); }

  /* Front side */
  .card--front { top: 527px; background: var(--paper); }
  .logo { position: absolute; left: 44px; top: 40px; display: flex; align-items: center; gap: 16px; }
  .logo .logo-dot { width: 58px; height: 58px; border-radius: 50%; background: var(--red); }
  .logo .brand-name { font-size: 26px; font-weight: 700; letter-spacing: 1px; color: var(--ink); }

  .divider { position: absolute; left: 70px; top: 236px; width: 640px; height: 1px; background: var(--rule); }
  .person { position: absolute; right: 70px; top: 170px; text-align: right; }
  .person .name { font-size: 24px; font-weight: 700; color: var(--red); line-height: 1.1; }
  .person .role { font-size: 19px; color: var(--ink); margin-top: 4px; }

  .contacts { position: absolute; left: 44px; top: 250px; list-style: none; }
  .contacts li { display: flex; align-items: center; gap: 10px; font-size: 17px; color: var(--ink); line-height: 25px; }
  .contacts svg { width: 15px; height: 15px; flex: none; }

  .address { position: absolute; right: 70px; top: 262px; text-align: right; font-size: 19px; color: var(--ink); line-height: 26px; }

  .footer-band { position: absolute; left: 0; bottom: 0; width: 760px; height: 82px; }
  .footer-web {
    position: absolute; right: 40px; bottom: 14px;
    font-size: 19px; color: var(--white); letter-spacing: .3px;
  }
</style>
</head>
<body>
<main class="stage">

  <section class="card card--back" aria-label="Card back">
    <div class="brand-disc"></div>
    <div class="brand-name">O VITALIS SYSTEMS</div>
    <div class="website">www.<span>quorvexsystems</span>.example</div>
  </section>

  <section class="card card--front" aria-label="Card front">
    <div class="logo">
      <div class="logo-dot"></div>
      <div class="brand-name">O VITALIS SYSTEMS</div>
    </div>

    <div class="person">
      <div class="name">Odile Brevard</div>
      <div class="role">chef de Projet</div>
    </div>
    <div class="divider"></div>

    <ul class="contacts">
      <li>
        <svg viewBox="0 0 16 16"><path d="M4 1l2.5 3-1.5 2c1 2 2.5 3.5 4.5 4.5l2-1.5 3 2.5-1.5 2.5C7 14 2 9 1.5 3.5z" fill="var(--red)"/></svg>
        +33 (0) 327 481 605
      </li>
      <li>
        <svg viewBox="0 0 16 16"><rect x="4" y="1" width="8" height="14" rx="1.5" fill="none" stroke="var(--red)" stroke-width="1.5"/><circle cx="8" cy="12.5" r="0.9" fill="var(--red)"/></svg>
        06 42 19 37 64
      </li>
      <li>
        <svg viewBox="0 0 16 16"><rect x="1" y="3" width="14" height="10" fill="none" stroke="var(--red)" stroke-width="1.5"/><path d="M1 3l7 6 7-6M1 13l5-5M15 13l-5-5" fill="none" stroke="var(--red)" stroke-width="1.3"/></svg>
        o.brevard@o-vitalissystems.example
      </li>
    </ul>

    <div class="address">318 Gaston Lemaire Street<br>59710 VERLANCOURT</div>

    <svg class="footer-band" viewBox="0 0 760 82" preserveAspectRatio="none" aria-hidden="true">
      <polygon points="0,8 470,8 450,28 0,28" fill="var(--red)"/>
      <polygon points="0,36 440,36 470,16 760,16 760,82 0,82" fill="var(--charcoal)"/>
    </svg>
    <div class="footer-web">www.quorvexsystems.example</div>
  </section>

</main>
</body>
</html>
```